Employee Benefits and Insurance Consulting

We are an existing company with over 30 years experience but are changing our name. We would like a simple design with grey tones.

Industry/Entity Type

Insurance

Contact Information for Business Card

Marlow Benefits Consulting
Gerald P Hollins CEO
5172 Brackenridge Road
Carroway, TN 37812
gerald@marlowbenefits-example.com
865-412-5593 - O
865-247-3861 - C

```html
<!DOCTYPE html>
<html lang="en">
<head>
<meta charset="utf-8">
<title>Marlow Benefits Consulting – Business Card</title>
<link rel="stylesheet" href="https://fonts.googleapis.com/css2?family=Arimo:ital,wght@0,400;1,400&display=swap">
<style>
  :root {
    --backdrop: #d9dadb;
    --card-grey: #a7a8aa;
    --card-white: #eef0f0;
    --ribbon-light: #c6c7c9;
    --ribbon-dark: #6e6f71;
    --brand-grey: #6a6b6d;
    --ink: #1e1e1e;
    --ink-soft: #444;
  }
  html, body {
    margin: 0;
    width: 1200px;
    height: 799px;
    overflow: hidden;
    background: var(--backdrop);
    font-family: "Arimo", Arial, sans-serif;
  }
  .business-card {
    position: absolute;
    left: 100px;
    top: 130px;
    width: 1000px;
    height: 540px;
    background: var(--card-grey);
    box-shadow: 0 10px 30px rgba(0,0,0,0.18);
    overflow: hidden;
  }
  .card-shapes {
    position: absolute;
    inset: 0;
  }
  .brand {
    position: absolute;
    left: 200px;
    top: 220px;
    display: flex;
    align-items: center;
    gap: 16px;
  }
  .brand-dot {
    width: 40px;
    height: 40px;
    border-radius: 50%;
    background: var(--brand-grey);
    flex: none;
  }
  .brand-name {
    margin: 0;
    font-size: 34px;
    font-weight: 400;
    line-height: 1.15;
    color: var(--brand-grey);
    letter-spacing: 0.5px;
  }
  .holder {
    position: absolute;
    left: 690px;
    top: 128px;
  }
  .holder-name {
    margin: 0;
    font-size: 32px;
    font-weight: 400;
    color: var(--ink);
  }
  .holder-title {
    margin: 2px 0 0 80px;
    font-size: 16px;
    font-style: italic;
    color: var(--ink-soft);
  }
  .contact-list {
    position: absolute;
    left: 690px;
    top: 252px;
    margin: 0;
    padding: 0;
    list-style: none;
  }
  .contact-list li {
    display: flex;
    align-items: center;
    gap: 10px;
    height: 28px;
    font-size: 17px;
    color: var(--ink-soft);
  }
  .contact-list .email { font-size: 14px; }
  .contact-icon { width: 17px; height: 17px; flex: none; }
  .address {
    position: absolute;
    left: 690px;
    top: 378px;
    margin: 0;
    font-style: normal;
    font-size: 21px;
    line-height: 1.4;
    color: var(--ink);
  }
</style>
</head>
<body>
  <div class="business-card">
    <svg class="card-shapes" width="1000" height="540" viewBox="0 0 1000 540" aria-hidden="true">
      <path class="white-panel" fill="var(--card-white)"
            d="M0,0 H700 C890,0 990,130 990,270 C990,420 880,540 700,540 H0 Z"/>
      <polygon class="ribbon-dark" fill="var(--ribbon-dark)" points="112,0 176,0 176,415 124,505 112,480"/>
      <polygon class="ribbon-light" fill="var(--ribbon-light)" points="20,0 118,0 118,405 96,490 20,410"/>
    </svg>

    <div class="brand">
      <span class="brand-dot"></span>
      <p class="brand-name">Marlow Benefits<br>Consulting</p>
    </div>

    <div class="holder">
      <p class="holder-name">Gerald P Hollins</p>
      <p class="holder-title">(CEO)</p>
    </div>

    <ul class="contact-list">
      <li>
        <svg class="contact-icon" viewBox="0 0 18 18" aria-hidden="true">
          <circle cx="9" cy="9" r="8" fill="none" stroke="#333" stroke-width="1.6"/>
          <rect x="6.5" y="4" width="5" height="10" rx="1" fill="#333"/>
        </svg>
        <span>865-247-3861</span>
      </li>
      <li>
        <svg class="contact-icon" viewBox="0 0 18 18" aria-hidden="true">
          <circle cx="9" cy="9" r="8.5" fill="#333"/>
          <path d="M6,4.5 L7.8,6.5 L6.9,7.8 C7.6,9.3 8.7,10.4 10.2,11.1 L11.5,10.2 L13.5,12 L12.4,13.5 C8.5,13.2 4.8,9.5 4.5,5.6 Z" fill="#eef0f0"/>
        </svg>
        <span>865-412-5593</span>
      </li>
      <li class="email">
        <svg class="contact-icon" viewBox="0 0 18 18" aria-hidden="true">
          <rect x="1" y="4" width="16" height="11" fill="#333"/>
          <path d="M1.5,4.5 L9,10 L16.5,4.5" fill="none" stroke="#eef0f0" stroke-width="1.3"/>
        </svg>
        <span>gerald@marlowbenefits-example.com</span>
      </li>
    </ul>

    <address class="address">
      5172 Brackenridge Road<br>
      Carroway, TN 37812
    </address>
  </div>
</body>
</html>
```